Harborline Business Card Designs***

WE ARE A FULL SERVICE FACILITY. ALL KINDS OF CAR/ TRK, REPAIR. CUSTOM WHEELS & TIRES. BRAKES, MUFFLERS, SHOCK, STRUTS...BATTERIES, STARTERS, ATERNATORS, TUNE UPS (WE DO IT ALL) ESTABLISHED IN 2004, LOCALLY OWNED AND OPERATED.... I AM OPEN TO SUGGESTIONS AS WELL ON ANY IDEAS

Contact Information for Business Card

WE DO COMPLETE AUTO REPAIR AND WHEELS, TIRES AND ACCESSORIES AT OUR STORE. I NAME OF SHOP (HARBORLINE AUTOMOTIVE GROUP) WOULD LIKE OUR EMAIL ON IT (HARBORLINEAUTOGROUP@QUVIX.NET) PHONE NUMBER 567-302-GEAR (4327) BUSINESS HOURS MON- FRI 8:00-6 SNAPGRID LOGO WITH (@HARBORLINE_AUTO_WESTRIDGE) WEBSITE (KESTRELROADWORKS.NET)FRIENDLOOP LOGO W/ (FRIENDLOOP.NET/HARBORLINEAUTOMOTIVE) AN A+/ QCR LOGO (THE LITTLE TORCH)... MAYBE EVEN EST.2009 INSIDE OF A "POW SIGN" (UNLESS IT GETS TO CLUTTERED) AND ON THE BACK OF THE CARD MAYBE A FAINT PICTURE OF "SOMETHING" IN BACKGROUND BUT STILL BE ABLE TO SEE THE ESTIMATE WE WRITE ON THE BACK. I WOULD LIKE ON THE BACK, DOWN IN THE RIGHT HAND CORNER A SPOT FOR A DATE AND INT. WE ALSO EXCEPT: ORBA, TRUSTPLATE, KELMORE AND ZINCWAY

```html
<!DOCTYPE html>
<html lang="en">
<head>
<meta charset="utf-8">
<title>Harborline Automotive Group – Business Card</title>
<link href="https://fonts.googleapis.com/css2?family=Krona+One&family=Montserrat:wght@400&family=Roboto+Condensed:wght@400;700&display=swap" rel="stylesheet">
<style>
  :root {
    --page: #e9e9e7;
    --card: #f1f1f1;
    --brand-blue: #1565b8;
    --hours-blue: #2e3a8c;
    --ink: #2b2b2b;
    --muted: #9a9a9a;
    --rule: #4a4a4a;
    --burst: #1aaee8;
    --photo-a: #dcdcdc;
    --photo-b: #c9c9cb;
    --badge: #2f8fa8;
  }
  * { box-sizing: border-box; margin: 0; padding: 0; }
  html, body { width: 1178px; height: 1200px; overflow: hidden; }
  body { background: var(--page); position: relative; font-family: "Roboto Condensed", sans-serif; color: var(--ink); }

  .card {
    position: absolute; width: 772px; height: 464px;
    background: var(--card); overflow: hidden;
  }
  .card--front { top: 66px; left: 217px; }
  .card--back { top: 635px; left: 229px; }

  .photo-fill { position: absolute; inset: 0; }
  .card--front .photo-fill {
    background: radial-gradient(ellipse at 55% 30%, #e3dada 0%, var(--photo-a) 40%, var(--photo-b) 100%);
    opacity: .55;
  }
  .card--back .photo-fill {
    background: linear-gradient(180deg, var(--photo-b) 0%, var(--photo-a) 45%, var(--photo-b) 100%);
    opacity: .45;
  }

  .wordmark { position: absolute; text-align: center; white-space: nowrap; }
  .wordmark__name {
    font-family: "Krona One", sans-serif; color: var(--brand-blue); line-height: 1;
  }
  .wordmark__tag {
    font-family: "Montserrat", sans-serif; color: var(--ink); line-height: 1;
  }
  .card--front .wordmark { top: 150px; left: 0; right: 0; }
  .card--front .wordmark__name { font-size: 44px; }
  .card--front .wordmark__tag { font-size: 33px; letter-spacing: 5px; margin-top: 12px; }

  .hours {
    position: absolute; top: 250px; left: 0; right: 0; text-align: center;
    font-size: 23px; color: var(--hours-blue);
  }

  .rule {
    position: absolute; height: 3px;
    background: linear-gradient(90deg, transparent, var(--rule) 15%, var(--rule) 85%, transparent);
  }
  .card--front .rule { top: 303px; left: 36px; right: 12px; }

  .contact-row {
    position: absolute; left: 0; right: 0; display: flex; justify-content: center; align-items: center;
    font-size: 18px; color: var(--ink);
  }
  .contact-row--primary { top: 328px; height: 32px; }
  .contact-row--social { top: 381px; height: 34px; }
  .contact-item { display: flex; align-items: center; gap: 7px; padding: 0 11px; }
  .contact-item + .contact-item { border-left: 1px solid var(--rule); }
  .contact-row--social .contact-item { padding: 4px 26px; }
  .icon { width: 26px; height: 26px; flex: none; }
  .brand-label { font-weight: 700; color: var(--ink); }
  .brand-square { width: 14px; height: 14px; background: var(--ink); flex: none; }
  .listing-badge { width: 24px; height: 32px; background: var(--badge); border-radius: 3px; }

  .logo-band {
    position: absolute; top: 193px; left: 0; right: 0; height: 142px;
    background: rgba(255,255,255,.75);
  }
  .card--back .wordmark { top: 202px; left: 60px; width: 430px; }
  .card--back .wordmark__name { font-size: 33px; }
  .card--back .wordmark__tag { font-size: 24px; letter-spacing: 3px; margin-top: 8px; }
  .est-burst { position: absolute; left: 505px; top: 188px; width: 160px; height: 74px; }
  .card--back .rule { top: 333px; left: 24px; right: 24px; }

  .payments {
    position: absolute; top: 366px; left: 89px; display: flex; gap: 16px; align-items: center;
  }
  .payment { display: flex; align-items: center; gap: 6px; font-size: 17px; font-weight: 700; color: var(--ink); }
  .payment__mark { width: 14px; height: 14px; background: var(--brand-blue); }
  .payment__mark--round { border-radius: 50%; background: #c9a23a; }

  .estimate-fields {
    position: absolute; top: 356px; left: 545px; font-size: 17px; line-height: 22px; color: var(--ink);
  }
  .estimate-fields .placeholder { color: var(--muted); }
</style>
</head>
<body>

<section class="card card--front">
  <div class="photo-fill" role="img" aria-label="Faint photo of a chrome engine bay with air cleaner"></div>

  <div class="wordmark">
    <div class="wordmark__name">HARBORLINE</div>
    <div class="wordmark__tag">AUTOMOTIVE GROUP</div>
  </div>

  <p class="hours">BUSINESS HOURS MON- FRI 8:00-6</p>
  <div class="rule"></div>

  <div class="contact-row contact-row--primary">
    <div class="contact-item">
      <svg class="icon" viewBox="0 0 24 24"><path fill="#2b2b2b" d="M6.6 10.8a15.1 15.1 0 0 0 6.6 6.6l2.2-2.2c.3-.3.7-.4 1-.2 1.1.4 2.3.6 3.6.6.6 0 1 .4 1 1V20c0 .6-.4 1-1 1A17 17 0 0 1 3 4c0-.6.4-1 1-1h3.5c.6 0 1 .4 1 1 0 1.3.2 2.5.6 3.6.1.3 0 .7-.2 1z"/></svg>
      <span>567-302-Gear (4327)</span>
    </div>
    <div class="contact-item">
      <svg class="icon" viewBox="0 0 40 40" style="width:40px;height:30px"><circle cx="20" cy="20" r="17" fill="#2b2b2b"/><text x="20" y="25" font-family="Roboto Condensed, sans-serif" font-size="14" font-weight="700" fill="#fff" text-anchor="middle">www</text></svg>
      <span>kestrelroadworks.net</span>
    </div>
    <div class="contact-item">
      <svg class="icon" viewBox="0 0 32 24" style="width:34px"><rect x="1" y="2" width="30" height="20" fill="#2b2b2b"/><path d="M2 3 16 14 30 3M2 21l10-9M30 21l-10-9" stroke="#fff" stroke-width="2" fill="none"/></svg>
      <span>harborlineautogroup@quvix.net</span>
    </div>
  </div>

  <div class="contact-row contact-row--social">
    <div class="contact-item">
      <span class="brand-square"></span><span class="brand-label">Snapgrid</span>
      <span>harborline_auto_westridge</span>
    </div>
    <div class="contact-item">
      <span class="brand-square"></span><span class="brand-label">Friendloop</span>
      <span>harborlineautomotive</span>
    </div>
    <div class="contact-item">
      <span class="listing-badge" role="img" aria-label="Accredited business listing badge"></span>
    </div>
  </div>
</section>

<section class="card card--back">
  <div class="photo-fill" role="img" aria-label="Faint photo of rows of custom alloy wheels"></div>
  <div class="logo-band"></div>

  <div class="wordmark">
    <div class="wordmark__name">HARBORLINE</div>
    <div class="wordmark__tag">AUTOMOTIVE GROUP</div>
  </div>

  <svg class="est-burst" viewBox="0 0 166 78" aria-label="Established 2009">
    <polygon fill="var(--burst)" points="2,38 28,30 22,12 54,22 78,2 92,20 128,10 122,30 164,40 126,48 136,70 100,58 84,76 66,56 26,66 34,48"/>
    <text x="83" y="47" font-family="Roboto Condensed, sans-serif" font-size="25" fill="#fff" text-anchor="middle">EST.2009</text>
  </svg>

  <div class="rule"></div>

  <div class="payments">
    <div class="payment"><span class="payment__mark payment__mark--round"></span>Zincway</div>
    <div class="payment"><span class="payment__mark"></span>Trustplate</div>
    <div class="payment"><span class="payment__mark"></span>Orba</div>
    <div class="payment"><span class="payment__mark"></span>Kelmore</div>
  </div>

  <div class="estimate-fields">
    <div>DATE : <span class="placeholder">DD/MM/YYYY</span></div>
    <div>INT :</div>
  </div>
</section>

</body>
</html>
```